Business Card Design

I am an Event and Wedding Planner in need of an eye catching business card featuring my logo (attached), my contact details, and my company tagline (Making every celebration glow with wonder...) I would like the tagline in font similar the logo's font.
Updates
I have just noticed that my logo has a misspelling so for the final design, I will be uploading a corrected logo as soon as I have it.
My apologies.
Reason: Waiting on a corrected logo...Lantern is misspelled and it should say Weddings not Wedding
The logo has been corrected so now Lantern is spelled correctly and it says Weddings instead of Wedding. Please use Edwardian Script ITC as the font for the tagline so it will match the logo. Thank you for your patience.
Target Market(s)
Engaged couples and people hosting milestone celebrations. 25-50 years old, predominately female
Industry/Entity Type
Business
Contact Information for Business Card
Rosalind Merrow, Event Manager / Owner, Mobile: 0491 868 254, Email: rosalind@velvetlanternco.com.au, www.velvetlanternco.com.au, Making every celebration glow with wonder...

```html
<!DOCTYPE html>
<html lang="en">
<head>
<meta charset="utf-8">
<title>Velvet Lantern – Business Card</title>
<link rel="stylesheet" href="https://fonts.googleapis.com/css2?family=Exo+2:wght@400;500&family=Pinyon+Script&display=swap">
<style>
  :root {
    --page-bg: #d4d0ca;
    --card-top: #f6f5f2;
    --card-bottom: #e3e0db;
    --ink: #2f2e2c;
    --ink-soft: #3d3c3a;
    --accent-red: #c7343a;
    --band-black: #111111;
    --rule: #8c8a87;
    --white: #ffffff;
  }
  * { margin: 0; padding: 0; box-sizing: border-box; }
  html, body {
    width: 1200px; height: 768px; overflow: hidden;
    background: var(--page-bg);
    font-family: "Exo 2", "Trebuchet MS", sans-serif;
  }
  .card {
    position: absolute; left: 100px; top: 94px;
    width: 1000px; height: 580px;
    border-radius: 26px; overflow: hidden;
    background: linear-gradient(160deg, var(--card-top) 0%, var(--card-bottom) 100%);
    box-shadow: 0 10px 30px rgba(0,0,0,0.18);
    color: var(--ink);
  }
  .brand-block {
    position: absolute; left: 492px; top: 70px; width: 460px;
    text-align: center;
  }
  .brand {
    font-size: 56px; font-weight: 400; color: var(--ink);
    letter-spacing: 1px; line-height: 1.1;
  }
  .brand-rule {
    width: 320px; height: 1px; margin: 30px auto 0;
    background: var(--ink-soft);
  }
  .tagline {
    margin-top: 8px;
    font-family: "Pinyon Script", "Edwardian Script ITC", cursive;
    font-size: 29px; line-height: 1.3; color: var(--ink);
    white-space: nowrap;
  }
  .holder-name {
    position: absolute; left: 41px; top: 192px;
    font-size: 27px; font-weight: 500; letter-spacing: 2px; color: var(--ink-soft);
    text-transform: uppercase;
  }
  .holder-title {
    position: absolute; left: 41px; top: 240px;
    font-size: 21px; font-weight: 500; color: var(--accent-red); letter-spacing: 0.5px;
  }
  .divider {
    position: absolute; left: 60px; top: 290px; width: 870px; height: 2px;
    background: linear-gradient(90deg, rgba(140,138,135,0) 0%, var(--rule) 30%, var(--rule) 75%, rgba(140,138,135,0) 100%);
  }
  .address {
    position: absolute; left: 41px; top: 382px;
    font-size: 21px; line-height: 32px; color: var(--ink-soft); letter-spacing: 0.5px;
  }
  .contact-list {
    position: absolute; right: 38px; top: 306px;
    list-style: none; text-align: right;
  }
  .contact-list li {
    display: flex; justify-content: flex-end; align-items: center; gap: 12px;
    color: var(--ink-soft); letter-spacing: 1px;
  }
  .contact-list .phone { font-size: 21px; height: 48px; }
  .contact-list .web-line { font-size: 18px; height: 34px; letter-spacing: 0.5px; }
  .contact-list svg { width: 22px; height: 22px; flex: none; fill: var(--ink-soft); }
  .bands { position: absolute; left: 0; bottom: 0; width: 1000px; height: 70px; }
  .band-url {
    position: absolute; left: 41px; bottom: 20px;
    font-size: 19px; font-weight: 500; color: var(--white); letter-spacing: 0.5px;
  }
</style>
</head>
<body>
  <section class="card" aria-label="Velvet Lantern business card">
    <div class="brand-block">
      <div class="brand">Velvet Lantern</div>
      <div class="brand-rule"></div>
      <p class="tagline">Making every celebration glow with wonder...</p>
    </div>

    <h1 class="holder-name">Rosalind Merrow</h1>
    <p class="holder-title">Event Manager / Owner</p>
    <div class="divider"></div>

    <p class="address">Suite 3, 14 Harbourview Lane<br>Brindlebay</p>

    <ul class="contact-list">
      <li class="phone">0491 868 254
        <svg viewBox="0 0 24 24" aria-hidden="true"><path d="M6.6 10.8a15.1 15.1 0 0 0 6.6 6.6l2.2-2.2a1 1 0 0 1 1-.25 11.4 11.4 0 0 0 3.6.57 1 1 0 0 1 1 1V20a1 1 0 0 1-1 1A17 17 0 0 1 3 4a1 1 0 0 1 1-1h3.5a1 1 0 0 1 1 1c0 1.250.2 2.45.57 3.57a1 1 0 0 1-.25 1z"/></svg>
      </li>
      <li class="phone">02 7140 3386
        <svg viewBox="0 0 24 24" aria-hidden="true"><path d="M7 1h10a2 2 0 0 1 2 2v18a2 2 0 0 1-2 2H7a2 2 0 0 1-2-2V3a2 2 0 0 1 2-2zm0 3v14h10V4zm5 15.2a1.1 1.1 0 1 0 0 2.2 1.1 1.1 0 0 0 0-2.2z"/></svg>
      </li>
      <li class="phone">02 7140 3387
        <svg viewBox="0 0 24 24" aria-hidden="true"><path d="M3 8h3v14H3zM8 2h10v6h3v14H8zm2 2v4h6V4zm0 7v2h2v-2zm4 0v2h2v-2zm-4 4v2h2v-2zm4 0v2h2v-2zm4-4v2h1v-2zm0 4v2h1v-2z"/></svg>
      </li>
      <li class="web-line">rosalind@velvetlanternco.com.au
        <svg viewBox="0 0 24 24" aria-hidden="true"><path d="M2 5h20v14H2zm2 2v.5l8 5 8-5V7zm0 2.8V17h16V9.8l-8 5z"/></svg>
      </li>
      <li class="web-line">www.velvetlanternco.com.au
        <svg viewBox="0 0 24 24" aria-hidden="true"><path d="M12 2a10 10 0 1 0 0 20 10 10 0 0 0 0-20zm6.9 6h-3a15 15 0 0 0-1.4-3.9A8 8 0 0 1 18.9 8zM12 4a13 13 0 0 1 1.9 4h-3.8A13 13 0 0 1 12 4zM4.3 14a8 8 0 0 1 0-4h3.4a16 16 0 0 0 0 4zm.8 2h3a15 15 0 0 0 1.4 3.9A8 8 0 0 1 5.1 16zm3-8h-3a8 8 0 0 1 4.4-3.9A15 15 0 0 0 8.1 8zM12 20a13 13 0 0 1-1.9-4h3.8A13 13 0 0 1 12 20zm2.3-6H9.7a14 14 0 0 1 0-4h4.6a14 14 0 0 1 0 4zm.2 5.9a15 15 0 0 0 1.4-3.9h3a8 8 0 0 1-4.4 3.9zm1.8-5.9a16 16 0 0 0 0-4h3.4a8 8 0 0 1 0 4z"/></svg>
      </li>
    </ul>

    <svg class="bands" viewBox="0 0 1000 70" aria-hidden="true">
      <path d="M395 22 H1000 V70 H395 Z" fill="var(--band-black)"/>
      <path d="M0 4 H372 C398 4 404 22 420 48 C428 62 434 70 440 70 H0 Z" fill="#9a9895"/>
      <path d="M0 4 H364 C390 4 396 22 410 48 C418 62 424 70 430 70 H0 Z" fill="var(--accent-red)"/>
    </svg>
    <span class="band-url">www.velvetlanternco.com.au</span>
  </section>
</body>
</html>
```